New Zealand Marlborough Sauvignon Blanc wine packaging design

We need packaging design for our new wine brand, Dunmore Vale. The wine is a New Zealand Marlborough Sauvignon Blanc. We would like the packaging will portray elegance and style with an understated label. We are looking for a label that portrays the elegance of the French Riviera. The label should be round or pill shaped.
Updates

Industry/Entity Type

Wine

Font styles to use
Serif
Sans Serif

Requirements
Must have
• The words in order of importance: Dunmore Vale, Sauvignon Blanc, Marlborough, New Zealand. It should be fit to the bottle posted in the links
Nice to have
• a pill shape or circular shape
Should not have
• Illustrations of wine bottles, wine glasses, or grapes

```html
<!DOCTYPE html>
<html lang="en">
<head>
<meta charset="UTF-8">
<title>Dunmore Vale — Marlborough Sauvignon Blanc Label</title>
<link href="https://fonts.googleapis.com/css2?family=Inter+Tight:wght@500;800&display=swap" rel="stylesheet">
<style>
  :root {
    --label-green: #97bf1e;
    --ink-white: #ffffff;
    --page-bg: #ffffff;
  }
  * { margin: 0; padding: 0; box-sizing: border-box; }
  html, body {
    width: 1200px;
    height: 675px;
    overflow: hidden;
    background: var(--page-bg);
  }
  .canvas {
    position: relative;
    width: 1200px;
    height: 675px;
  }
  .label {
    position: absolute;
    left: 408px;
    top: 55px;
    width: 385px;
    height: 565px;
    border-radius: 192.5px;
    background: var(--label-green);
    overflow: hidden;
    color: var(--ink-white);
    font-family: "Inter Tight", "Helvetica Neue", Arial, sans-serif;
  }
  .wordmark {
    position: absolute;
    left: 0;
    font-weight: 800;
    font-size: 98px;
    line-height: 1;
    letter-spacing: -5px;
    white-space: nowrap;
  }
  .wordmark--first { top: 196px; left: 2px; }
  .wordmark--second { top: 276px; left: 96px; }
  .vertical-text {
    position: absolute;
    writing-mode: vertical-rl;
    transform: rotate(180deg);
    font-weight: 500;
    white-space: nowrap;
    line-height: 1;
  }
  .varietal {
    left: 240px;
    top: 26px;
    font-size: 23px;
    letter-spacing: -0.3px;
  }
  .region {
    left: 246px;
    top: 360px;
    font-size: 15.5px;
    letter-spacing: -0.2px;
  }
</style>
</head>
<body>
  <main class="canvas">
    <section class="label" aria-label="Dunmore Vale Sauvignon Blanc wine label">
      <span class="vertical-text varietal">Sauvignon Blanc</span>
      <h1 class="wordmark wordmark--first">Dunmore</h1>
      <p class="wordmark wordmark--second">Vale</p>
      <span class="vertical-text region">Marlborough, New Zealand</span>
    </section>
  </main>
</body>
</html>
```